Property Developer Business card design

we need a business card design + printing for a new Property developer company based in melbourne.
We are a group of investors investing in a property developer business. We have more projects involved in residential property as opposed to commercial property but we are involved in both market. we also provide consulting services with overseas investors willing to invest in the australian property market.
Updates
I have uploaded the logo. I'm not very convince with the colors of my logo... any suggestion please?.
Thanks guys!
Target Market(s)
property investors or person willing to purchase investment property
Industry/Entity Type
Residential
Contact Information for Business Card
Bramblecourt Holdings Australia Pty Ltd
Look and feel

```html
<!DOCTYPE html>
<html lang="en">
<head>
<meta charset="utf-8">
<title>Bramblecourt Holdings Australia – Business Card</title>
<link href="https://fonts.googleapis.com/css2?family=Questrial&display=swap" rel="stylesheet">
<style>
  :root {
    --backdrop: #e9e7e3;
    --card: #ffffff;
    --brand-blue: #3385f5;
    --brand-red: #e2474f;
    --brand-deep-red: #d31f2b;
    --ink: #3a3a3a;
    --muted: #555555;
    --on-blue: #ffffff;
  }
  * { box-sizing: border-box; margin: 0; padding: 0; }
  html, body { width: 1200px; height: 1000px; overflow: hidden; }
  body {
    background: var(--backdrop);
    font-family: "Questrial", "Century Gothic", sans-serif;
    position: relative;
  }
  .card {
    position: absolute;
    left: 220px;
    width: 760px;
    height: 440px;
    background: var(--card);
    border-radius: 44px 8px 44px 8px;
    overflow: hidden;
    box-shadow: 0 6px 18px rgba(0,0,0,0.12);
  }
  .card--front { top: 40px; }
  .card--back { top: 520px; }

  .front-wave { position: absolute; inset: 0; width: 100%; height: 100%; }

  .company-name {
    position: absolute;
    left: 40px;
    top: 70px;
    width: 230px;
    color: var(--brand-blue);
    font-size: 22px;
    line-height: 1.2;
  }
  .person {
    position: absolute;
    right: 70px;
    top: 90px;
    text-align: right;
  }
  .person__name {
    font-size: 54px;
    color: var(--ink);
    letter-spacing: 0.5px;
  }
  .person__title {
    font-size: 15px;
    color: var(--brand-red);
    margin-top: 2px;
  }
  .contact-list {
    position: absolute;
    left: 40px;
    bottom: 30px;
    list-style: none;
    color: var(--on-blue);
    font-size: 14px;
    letter-spacing: 1.6px;
  }
  .contact-list li {
    display: flex;
    align-items: center;
    gap: 10px;
    line-height: 22px;
  }
  .contact-list svg { width: 13px; height: 13px; flex: none; }

  .back-bar {
    position: absolute;
    width: 16px;
  }
  .back-bar--blue { right: 0; top: 0; height: 190px; background: var(--brand-blue); }
  .back-bar--red { left: 0; bottom: 0; height: 200px; background: var(--brand-deep-red); }

  .back-brand {
    position: absolute;
    left: 0; right: 0;
    top: 150px;
    text-align: center;
  }
  .back-brand__mark {
    display: inline-block;
    width: 22px; height: 22px;
    border-radius: 50%;
    background: var(--brand-blue);
    vertical-align: middle;
    margin-right: 14px;
  }
  .back-brand__name {
    display: inline-block;
    vertical-align: middle;
    font-size: 40px;
    color: var(--brand-blue);
  }
  .back-web {
    position: absolute;
    left: 0; right: 0;
    top: 280px;
    text-align: center;
    font-size: 13px;
    letter-spacing: 7px;
    color: var(--muted);
  }
</style>
</head>
<body>

<section class="card card--front" aria-label="Business card front">
  <svg class="front-wave" viewBox="0 0 760 440" preserveAspectRatio="none" aria-hidden="true">
    <path d="M0,292 C150,202 300,252 430,272 C580,292 700,222 760,72" fill="none" stroke="var(--brand-red)" stroke-width="5"/>
    <path d="M0,300 C150,210 300,260 430,280 C580,300 700,230 760,80 L760,440 L0,440 Z" fill="var(--brand-blue)"/>
  </svg>

  <div class="company-name">Bramblecourt Holdings Australia</div>

  <div class="person">
    <div class="person__name">Daniel Harwood</div>
    <div class="person__title">Managing Director</div>
  </div>

  <ul class="contact-list">
    <li>
      <svg viewBox="0 0 12 12"><rect x="3" y="0.5" width="6" height="11" rx="1.2" fill="none" stroke="#fff" stroke-width="1.2"/></svg>
      0400 555 218
    </li>
    <li>
      <svg viewBox="0 0 12 12"><path d="M2,1 L4.5,1 L5.5,4 L4,5 C5,7 6,8 8,9 L9,7.5 L12,8.5 L12,11 C6,11 1,6 1,1 Z" fill="#fff"/></svg>
      +61 3 9000 4127
    </li>
    <li>
      <svg viewBox="0 0 12 12"><rect x="0.5" y="2.5" width="11" height="7.5" fill="none" stroke="#fff" stroke-width="1.2"/><path d="M0.5,2.5 L6,7 L11.5,2.5" fill="none" stroke="#fff" stroke-width="1.2"/></svg>
      daniel.harwood@bramblecourt.com.au
    </li>
    <li>
      <svg viewBox="0 0 12 12"><circle cx="6" cy="6" r="5" fill="none" stroke="#fff" stroke-width="1.2"/><path d="M1,6 H11 M6,1 C3,4 3,8 6,11 M6,1 C9,4 9,8 6,11" fill="none" stroke="#fff" stroke-width="1"/></svg>
      www.bramblecourtholdings.com.au
    </li>
    <li>
      <svg viewBox="0 0 12 12"><path d="M6,1 L11.5,6 L10,6 L10,11 L2,11 L2,6 L0.5,6 Z" fill="#fff"/></svg>
      12 Wattle Grove Court Tarneit VIC 3030
    </li>
  </ul>
</section>

<section class="card card--back" aria-label="Business card back">
  <div class="back-bar back-bar--blue"></div>
  <div class="back-bar back-bar--red"></div>

  <div class="back-brand">
    <span class="back-brand__mark"></span>
    <span class="back-brand__name">Bramblecourt Holdings Australia</span>
  </div>

  <div class="back-web">www.bramblecourtholdings.com.au</div>
</section>

</body>
</html>
```